KLV Plant Services

We are a heavy diesel mechanical business with additional air con certificates, remapping engine rebuilt

Contact Information for Business Card

Company Name, Director Name, Managing Director, Contact details, email and website

Font styles to use
Serif
Script

```html
<!DOCTYPE html>
<html lang="en">
<head>
<meta charset="utf-8">
<title>KLV Plant Services – Business Card</title>
<link rel="stylesheet" href="https://fonts.googleapis.com/css2?family=Noto+Serif:wght@400;700&display=swap">
<style>
  :root {
    --navy: #23206a;
    --navy-deep: #1f1c62;
    --ink: #1c1c1c;
    --ink-soft: #4a4a4a;
    --paper: #ffffff;
    --backdrop: #e9e8ec;
    --text: #2a2a2a;
  }
  * { box-sizing: border-box; margin: 0; padding: 0; }
  html, body { width: 1200px; height: 786px; overflow: hidden; }
  body {
    background: var(--backdrop);
    font-family: "Noto Serif", Georgia, serif;
    position: relative;
  }
  .card {
    position: absolute;
    top: 238px;
    width: 540px;
    height: 309px;
    box-shadow: 0 6px 18px rgba(0,0,0,0.18);
    overflow: hidden;
  }
  .card--front { left: 40px; background: var(--paper); }
  .card--back { left: 620px; background: var(--navy-deep); }

  .holder {
    position: absolute;
    top: 18px;
    right: 34px;
    text-align: right;
    color: var(--navy);
  }
  .holder__name { font-size: 19px; font-weight: 700; letter-spacing: 0.5px; line-height: 1.1; }
  .holder__role { font-size: 12px; margin-top: 2px; }
  .holder-bar {
    position: absolute;
    top: 20px; right: 0;
    width: 14px; height: 34px;
    background: var(--navy);
  }

  .machine-art {
    position: absolute;
    left: 320px;
    top: 96px;
    width: 190px;
    height: 213px;
    border-radius: 6px 6px 0 0;
    background: linear-gradient(180deg, var(--ink-soft), var(--ink));
  }

  .brand {
    position: absolute;
    display: flex;
    align-items: center;
    gap: 10px;
  }
  .brand__dot { border-radius: 50%; flex: none; }
  .brand__name { font-weight: 700; line-height: 1.1; white-space: nowrap; }
  .card--front .brand { left: 34px; top: 110px; }
  .card--front .brand__dot { width: 16px; height: 16px; background: var(--navy); }
  .card--front .brand__name { font-size: 22px; color: var(--navy); }

  .address {
    position: absolute;
    left: 40px;
    top: 188px;
    font-size: 14px;
    line-height: 1.35;
    color: var(--text);
  }
  .contacts {
    position: absolute;
    left: 40px;
    top: 234px;
    list-style: none;
    font-size: 14px;
    line-height: 1.45;
    color: var(--text);
  }
  .contacts li { display: flex; align-items: center; gap: 7px; white-space: nowrap; }
  .contacts svg { width: 12px; height: 12px; flex: none; }

  .card--back .brand {
    left: 0; right: 0; top: 0; bottom: 0;
    justify-content: center;
  }
  .card--back .brand__dot { width: 22px; height: 22px; background: var(--paper); }
  .card--back .brand__name { font-size: 34px; color: var(--paper); }
</style>
</head>
<body>
  <section class="card card--front">
    <div class="holder">
      <p class="holder__name">DANIEL REEVE</p>
      <p class="holder__role">Managing Director</p>
    </div>
    <div class="holder-bar"></div>

    <div class="machine-art" role="img" aria-label="Black silhouette of an excavator arm and bucket"></div>

    <div class="brand">
      <span class="brand__dot"></span>
      <span class="brand__name">KLV Plant Services</span>
    </div>

    <p class="address">Your address, City<br>State, Zip 1234</p>

    <ul class="contacts">
      <li>
        <svg viewBox="0 0 24 24" fill="var(--navy)"><path d="M6.6 10.8a15.5 15.5 0 0 0 6.6 6.6l2.2-2.2a1 1 0 0 1 1-.25 11.4 11.4 0 0 0 3.6.57 1 1 0 0 1 1 1V20a1 1 0 0 1-1 1A17 17 0 0 1 3 4a1 1 0 0 1 1-1h3.5a1 1 0 0 1 1 1c0 1.25.2 2.45.57 3.57a1 1 0 0 1-.25 1z"/></svg>
        123 456 789
      </li>
      <li>
        <svg viewBox="0 0 24 24" fill="none" stroke="var(--navy)" stroke-width="2.4"><rect x="3" y="5" width="18" height="14" rx="1"/><path d="M3 6l9 7 9-7"/></svg>
        info@yourmail.com
      </li>
      <li>
        <svg viewBox="0 0 24 24" fill="none" stroke="var(--navy)" stroke-width="2.2"><circle cx="12" cy="12" r="9"/><path d="M3 12h18M12 3c3 3 3 15 0 18M12 3c-3 3-3 15 0 18"/></svg>
        www.yourwebsite.com
      </li>
    </ul>
  </section>

  <section class="card card--back">
    <div class="brand">
      <span class="brand__dot"></span>
      <span class="brand__name">KLV Plant Services</span>
    </div>
  </section>
</body>
</html>
```